Executive & Leadership Coach needs a Graphic Design

We need a graphic design for a Leadership methodology/strategy that can be linked to The Harbor Prism

The Harbor Prism consists of:
1. Achievements
2. Personal Brand
3. Network
4. Executive Presence

This should Graphic Design will need to be used in PowerPoint presentations, training manuals and web pages

The design should be modern and provide the feeling of strength, trust, energy & creativity

Industry/Entity Type

Graphic Design

Font styles to use
Other font styles liked:
• Calibri, Verdana

```html
<!DOCTYPE html>
<html lang="en">
<head>
<meta charset="utf-8">
<title>The Harbor Prism</title>
<link rel="stylesheet" href="https://fonts.googleapis.com/css2?family=Open+Sans:wght@400;700&display=swap">
<style>
  :root {
    --canvas-bg: #ffffff;
    --ring: #ffffff;
    --ring-edge: #e3e3e3;
    --blue-deep: #1b6cbf;
    --blue-light: #27a9e1;
    --green-light: #cbdc2c;
    --green-deep: #8dc63f;
    --purple-light: #93278f;
    --purple-deep: #5e2d8f;
    --pink-deep: #e0186e;
    --pink-light: #ec008c;
    --label: #ffffff;
    --hub-text: #333333;
  }
  * { margin: 0; padding: 0; box-sizing: border-box; }
  html, body {
    width: 1200px;
    height: 1000px;
    overflow: hidden;
    background: var(--canvas-bg);
  }
  .prism-wheel {
    display: block;
    width: 1200px;
    height: 1000px;
  }
  .segment-label {
    font-family: "Open Sans", Calibri, sans-serif;
    font-size: 48px;
    font-weight: 400;
    fill: var(--label);
    letter-spacing: 0.5px;
  }
  .hub-title {
    font-family: "Open Sans", Calibri, sans-serif;
    font-size: 50px;
    font-weight: 700;
    fill: var(--hub-text);
  }
</style>
</head>
<body>
<svg class="prism-wheel" viewBox="0 0 1200 1000" xmlns="http://www.w3.org/2000/svg" role="img" aria-label="The Harbor Prism: Executive Presence, Achievements, Network, Personal">
  <defs>
    <linearGradient id="grad-presence" x1="0" y1="0" x2="1" y2="1">
      <stop offset="0" stop-color="var(--blue-deep)"/>
      <stop offset="1" stop-color="var(--blue-light)"/>
    </linearGradient>
    <linearGradient id="grad-achievements" x1="0" y1="1" x2="1" y2="0">
      <stop offset="0" stop-color="var(--green-light)"/>
      <stop offset="0.5" stop-color="var(--green-deep)"/>
      <stop offset="1" stop-color="var(--green-deep)"/>
    </linearGradient>
    <linearGradient id="grad-network" x1="0" y1="0" x2="1" y2="1">
      <stop offset="0" stop-color="var(--purple-light)"/>
      <stop offset="0.6" stop-color="var(--purple-deep)"/>
    </linearGradient>
    <linearGradient id="grad-personal" x1="0" y1="1" x2="1" y2="0">
      <stop offset="0" stop-color="var(--pink-deep)"/>
      <stop offset="1" stop-color="var(--pink-light)"/>
    </linearGradient>
    <filter id="soft-shadow" x="-20%" y="-20%" width="140%" height="140%">
      <feDropShadow dx="0" dy="4" stdDeviation="8" flood-color="#000" flood-opacity="0.18"/>
    </filter>
    <filter id="hub-shadow" x="-30%" y="-30%" width="160%" height="160%">
      <feDropShadow dx="0" dy="3" stdDeviation="6" flood-color="#000" flood-opacity="0.22"/>
    </filter>

    <path id="arc-presence" d="M292,500 A308,308 0 0 1 600,192"/>
    <path id="arc-achievements" d="M600,192 A308,308 0 0 1 908,500"/>
    <path id="arc-personal" d="M254,500 A346,346 0 0 0 600,846"/>
    <path id="arc-network" d="M600,846 A346,346 0 0 0 946,500"/>
  </defs>

  <!-- outer ring -->
  <circle class="outer-ring" cx="600" cy="500" r="432" fill="var(--ring)" stroke="var(--ring-edge)" stroke-width="1.5" filter="url(#soft-shadow)"/>

  <!-- segments -->
  <g class="segments" stroke="var(--ring)" stroke-width="3">
    <path class="segment segment-presence" d="M600,500 L200,500 A400,400 0 0 1 600,100 Z" fill="url(#grad-presence)"/>
    <path class="segment segment-achievements" d="M600,500 L600,100 A400,400 0 0 1 1000,500 Z" fill="url(#grad-achievements)"/>
    <path class="segment segment-network" d="M600,500 L1000,500 A400,400 0 0 1 600,900 Z" fill="url(#grad-network)"/>
    <path class="segment segment-personal" d="M600,500 L600,900 A400,400 0 0 1 200,500 Z" fill="url(#grad-personal)"/>
  </g>

  <!-- labels -->
  <text class="segment-label"><textPath href="#arc-presence" startOffset="50%" text-anchor="middle">Executive Presence</textPath></text>
  <text class="segment-label"><textPath href="#arc-achievements" startOffset="50%" text-anchor="middle">Achievements</textPath></text>
  <text class="segment-label"><textPath href="#arc-personal" startOffset="50%" text-anchor="middle">Personal</textPath></text>
  <text class="segment-label"><textPath href="#arc-network" startOffset="50%" text-anchor="middle">Network</textPath></text>

  <!-- hub -->
  <circle class="hub-ring" cx="600" cy="500" r="150" fill="var(--ring)" filter="url(#hub-shadow)"/>
  <circle class="hub" cx="600" cy="500" r="140" fill="var(--ring)" stroke="var(--ring-edge)" stroke-width="2"/>
  <text class="hub-title" x="600" y="492" text-anchor="middle">Harbor</text>
  <text class="hub-title" x="600" y="552" text-anchor="middle">Prism</text>
</svg>
</body>
</html>
```